Kestrel Facilities Business Card Design

We would now like to design business cards with the new Kestrel Facilities logo

Target Market(s)

Professional

Industry/Entity Type

Professional services

Contact Information for Business Card

Employee name, title, phone number, email address, corporate office address and logo.

Font styles to use
Sans Serif

Colors
0054AA
0677BA
7BADD7
CADEEF
E8F1F8

Requirements
Must have
• My logo
Should not have
• any other pictures or images besides my logo

```html
<!DOCTYPE html>
<html lang="en">
<head>
<meta charset="utf-8">
<title>Kestrel Facilities Business Card</title>
<link rel="stylesheet" href="https://fonts.googleapis.com/css2?family=Montserrat:wght@400;500&family=Oswald:wght@500;600&display=swap">
<style>
  :root {
    --backdrop: #9c9c9c;
    --brand-blue: #0a6fd8;
    --brand-blue-deep: #0054aa;
    --paper: #f4f4f4;
    --ink: #4a4a4a;
    --ink-soft: #6a6a6a;
  }
  * { box-sizing: border-box; margin: 0; padding: 0; }
  html, body { width: 1200px; height: 1050px; overflow: hidden; }
  body {
    background: var(--backdrop);
    font-family: "Montserrat", Arial, sans-serif;
    position: relative;
  }
  .card {
    position: absolute;
    left: 250px;
    width: 700px;
    height: 400px;
    border-radius: 3px;
    box-shadow: 0 14px 30px rgba(0,0,0,0.25);
  }
  .card-front {
    top: 90px;
    background: var(--paper);
    border-bottom: 4px solid var(--brand-blue);
  }
  .card-back {
    top: 560px;
    background: var(--brand-blue);
    display: flex;
    align-items: center;
    justify-content: center;
    gap: 18px;
  }
  .holder {
    position: absolute;
    right: 60px;
    top: 70px;
    text-align: right;
  }
  .holder-name {
    font-family: "Oswald", "Arial Narrow", sans-serif;
    font-weight: 600;
    font-size: 36px;
    letter-spacing: 1px;
    color: var(--brand-blue);
    text-transform: uppercase;
    line-height: 1.05;
  }
  .holder-title {
    font-size: 19px;
    color: var(--ink-soft);
    letter-spacing: 1px;
    margin-right: 14px;
  }
  .contact-row {
    position: absolute;
    left: 50px;
    right: 50px;
    bottom: 60px;
    display: flex;
    justify-content: space-between;
    align-items: flex-end;
  }
  .contact-item {
    text-align: center;
    font-size: 15px;
    line-height: 1.45;
    color: var(--ink);
    letter-spacing: 0.5px;
  }
  .contact-icon {
    display: block;
    width: 32px;
    height: 32px;
    margin: 0 auto 12px;
  }
  .brand-mark {
    width: 56px;
    height: 56px;
    background: #fff;
  }
  .brand-name {
    font-family: "Oswald", "Arial Narrow", sans-serif;
    font-weight: 500;
    font-size: 46px;
    color: #fff;
    letter-spacing: 2px;
    text-transform: uppercase;
  }
</style>
</head>
<body>
  <section class="card card-front">
    <div class="holder">
      <div class="holder-name">Daniel Harrow</div>
      <div class="holder-title">President</div>
    </div>
    <div class="contact-row">
      <div class="contact-item">
        <svg class="contact-icon" viewBox="0 0 32 32" aria-hidden="true">
          <rect width="32" height="32" fill="var(--brand-blue)"/>
          <path d="M16 7a6 6 0 0 0-6 6c0 4.5 6 11 6 11s6-6.5 6-11a6 6 0 0 0-6-6z" fill="#fff"/>
          <circle cx="16" cy="13" r="2.3" fill="var(--brand-blue)"/>
        </svg>
        4120 Alder Ridge Road<br>Larkspur, Alaska 99508
      </div>
      <div class="contact-item">
        <svg class="contact-icon" viewBox="0 0 32 32" aria-hidden="true">
          <rect width="32" height="32" fill="var(--brand-blue)"/>
          <path d="M12 8l3 4-2 2c1 2 3 4 5 5l2-2 4 3-2 3c-6 0-12-6-12-12z" fill="#fff"/>
        </svg>
        555-204-7731<br>555-318-6642
      </div>
      <div class="contact-item">
        <svg class="contact-icon" viewBox="0 0 32 32" aria-hidden="true">
          <rect width="32" height="32" fill="var(--brand-blue)"/>
          <rect x="7" y="10" width="18" height="12" fill="#fff"/>
          <path d="M7 10l9 7 9-7" fill="none" stroke="var(--brand-blue)" stroke-width="1.6"/>
        </svg>
        info@kestrelfacilities.com<br>www.kestrelfacilities.com
      </div>
    </div>
  </section>

  <section class="card card-back">
    <div class="brand-mark" aria-hidden="true"></div>
    <div class="brand-name">Kestrel Facilities</div>
  </section>
</body>
</html>
```